MBRDC redesign and update stationary bc envelopes.

Stationary, Envelopes, Brochures, Business Card. Need to add second surgeon and two other offices. I need everything to match. I am a oral & maxillofacial surgeon.
Additional surgeon and three office addresses.
Jae Min Park, DMD, MD, INC

3718 Silver Meadow Parkway
El Dorado Hills, CA 95762

642 Lorin Way, Suite 101
Folsom, CA. 95630

2317 Vale Street, Suite 105
Auburn, CA. 95603
Updates

Logo design uploaded. Zapfino Extra/Adobe Garamond/Palatino are fonts used before. Not sure what is on exisiting stationary.

Target Market(s)

Referral dentist and sometimes patients. I am a oral & Maxillofacial surgeon.

Industry/Entity Type

Dental Clinic

Font styles to use
Serif
Script

Requirements
Must have
• Color of existing stationary. Update is possible.
Nice to have
• Conservative/modern
Should not have
• Playful

```html
<!DOCTYPE html>
<html lang="en">
<head>
<meta charset="utf-8">
<title>MBRDC Business Card</title>
<link href="https://fonts.googleapis.com/css2?family=EB+Garamond:ital,wght@0,400;0,500;0,700;1,400&display=swap" rel="stylesheet">
<style>
  :root {
    --page: #e6e6e4;
    --front-bg: #edf3f7;
    --back-bg: #ffffff;
    --edge: #6b4f3f;
    --brown: #5a4034;
    --green: #6c9a2a;
    --ink: #3a3330;
    --rule: #8a8580;
  }
  * { box-sizing: border-box; margin: 0; padding: 0; }
  html, body { width: 1200px; height: 895px; overflow: hidden; }
  body {
    background: var(--page);
    font-family: "EB Garamond", Georgia, serif;
    color: var(--ink);
    position: relative;
  }
  .card {
    position: absolute;
    width: 620px;
    height: 354px;
    border-bottom: 9px solid var(--edge);
    box-shadow: 0 6px 18px rgba(0,0,0,.18);
  }
  .card--front { left: 60px; top: 50px; background: var(--front-bg); }
  .card--back { left: 520px; top: 480px; background: var(--back-bg); }

  .brand {
    display: flex; align-items: center; gap: 12px;
    font-weight: 500; color: var(--brown);
    letter-spacing: 3px;
  }
  .brand__dot { width: 18px; height: 18px; border-radius: 50%; background: var(--green); }

  .card--front .brand { position: absolute; left: 0; right: 0; top: 62px; justify-content: center; font-size: 52px; }

  .offices {
    position: absolute; left: 20px; right: 20px; top: 178px;
    display: flex; justify-content: space-between; text-align: center;
  }
  .office { font-size: 15px; line-height: 1.15; width: 190px; }
  .office svg { display: block; margin: 0 auto 4px; }
  .website {
    position: absolute; left: 0; right: 0; bottom: 28px; text-align: center;
    font-style: italic; font-size: 22px; color: var(--green); letter-spacing: .5px;
  }

  .card--back .brand { position: absolute; left: 36px; top: 92px; font-size: 40px; }
  .divider { position: absolute; left: 288px; top: 40px; width: 1px; height: 150px; background: var(--rule); }
  .details { position: absolute; left: 306px; top: 36px; }
  .surgeon { color: var(--green); font-weight: 700; font-size: 19px; line-height: 1.15; }
  .contact { list-style: none; margin-top: 14px; font-size: 15px; line-height: 1.35; }
  .contact li { display: flex; align-items: center; gap: 8px; }
  .services {
    position: absolute; left: 0; right: 0; bottom: 34px; text-align: center;
    font-size: 15px; line-height: 1.3;
  }
</style>
</head>
<body>
  <section class="card card--front">
    <div class="brand"><span class="brand__dot"></span>MBRDC</div>
    <div class="offices">
      <address class="office">
        <svg width="14" height="18" viewBox="0 0 14 18"><path d="M7 0C3 0 0 3 0 7c0 5 7 11 7 11s7-6 7-11c0-4-3-7-7-7z" fill="#6c9a2a"/><circle cx="7" cy="7" r="2.6" fill="#edf3f7"/></svg>
        3718 Silver Meadow Parkway<br>El Dorado Hills, CA 95762
      </address>
      <address class="office">
        <svg width="14" height="18" viewBox="0 0 14 18"><path d="M7 0C3 0 0 3 0 7c0 5 7 11 7 11s7-6 7-11c0-4-3-7-7-7z" fill="#6c9a2a"/><circle cx="7" cy="7" r="2.6" fill="#edf3f7"/></svg>
        642 Lorin Way, Suite 101<br>Folsom, CA. 95630
      </address>
      <address class="office">
        <svg width="14" height="18" viewBox="0 0 14 18"><path d="M7 0C3 0 0 3 0 7c0 5 7 11 7 11s7-6 7-11c0-4-3-7-7-7z" fill="#6c9a2a"/><circle cx="7" cy="7" r="2.6" fill="#edf3f7"/></svg>
        2317 Vale Street, Suite 105<br>Auburn, CA. 95603
      </address>
    </div>
    <p class="website">www.mbrdcsurgery.com</p>
  </section>

  <section class="card card--back">
    <div class="brand"><span class="brand__dot"></span>MBRDC</div>
    <div class="divider"></div>
    <div class="details">
      <p class="surgeon">Daniel R. Lowry, DDS, Inc.</p>
      <p class="surgeon">Jae Min Park, DMD, MD, Inc.</p>
      <ul class="contact">
        <li><svg width="13" height="12" viewBox="0 0 13 12"><path d="M1 4c0-2 2-3 5.5-3S12 2 12 4l-2.5.8L8.6 3H4.4l-.9 1.8zM2.5 6h8l1 5h-10z" fill="#5a4034"/></svg>916.555.0142</li>
        <li><svg width="13" height="12" viewBox="0 0 13 12"><rect x="3" y="0" width="7" height="4" fill="#5a4034"/><rect x="0" y="4" width="13" height="5" rx="1" fill="#5a4034"/><rect x="3" y="7" width="7" height="5" fill="#fff" stroke="#5a4034"/></svg>916.555.0187</li>
        <li><svg width="13" height="10" viewBox="0 0 13 10"><rect x=".5" y=".5" width="12" height="9" fill="none" stroke="#5a4034"/><path d="M.5.5l6 5 6-5" fill="none" stroke="#5a4034"/></svg>drlowry@mbrdcsurgery.com</li>
        <li><svg width="13" height="13" viewBox="0 0 13 13"><circle cx="6.5" cy="6.5" r="6" fill="none" stroke="#5a4034"/><ellipse cx="6.5" cy="6.5" rx="2.6" ry="6" fill="none" stroke="#5a4034"/><path d="M.5 6.5h12M1.5 3.5h10M1.5 9.5h10" stroke="#5a4034"/></svg>mbrdcsurgery.com</li>
      </ul>
    </div>
    <div class="services">
      <p>Dentoalveoral Surgery | Dental Implant Surgery | Orthognathic Surgery</p>
      <p>Facial Trauma Surgery | Preprosthetic and Reconstructive Surgery</p>
      <p>TMJ Disorders and Surgery | Obstructive Sleep Apnea Surgery</p>
    </div>
  </section>
</body>
</html>
```